Children’s entertainer/balloon artist Website Home Page and custom landing page

I need a home page design for the home page of a children and family entertainer/balloon twister’s website. I also need a custom landing page for family theatre shows performed by the same entertainer.
It will be a Wordpress website and I need the final artwork in a layer Photoshop file with all the layers clearly named and labeled.

Target Market(s)

The site visitors are mainly mums, aged between early 20’s and late 30’s. Other visitors will included companies for Christmas functions, and event organisers for corporate functions.

Industry/Entity Type

Entertainment

Number of Pages Required

2 page

Font styles to use
Sans Serif

Colors
34a6d7
f37122

Requirements
Must have
• Layout
• I have included a wireframe for the home page layout and the custom landing page for your reference. This is a guide only and I welcome your interpretation with the rough layout provided.
• This website needs to look good on all devices as it will be fully responsive.
• It needs to include a footer area on the page, that has social media and a call to action area included.
• Colours
• The main colours for the site is:
• orange (call to action colour)
• ff6800
• blue/turquoise
• 42abc3
• Pictures
• I have included images of the entertainer/balloon artist for you to use/take inspiration from.
• These images will be included on the website. I want to show lots of people having fun.
• I would like to have elements of the logo used in isolation across the website
• i.e. the octopus figure to be included in the footer or the bird element to be included in the testimonial slider etc.
• Elements to include
• Note: use the images of the entertainer in the boxes on the home page (balloon shows, balloon twisting, balloon workshops, theatre shows (the three little balloon pigs on his head)
Nice to have
Should not have
• Element to avoid
• Stock imagery of balloon sculptures - use images provided.

```html
<!DOCTYPE html>
<html lang="en">
<head>
<meta charset="utf-8">
<title>Benny Bounce – Children's Entertainer</title>
<link href="https://fonts.googleapis.com/css2?family=Lobster&family=Open+Sans:ital,wght@0,400;0,600;1,400&display=swap" rel="stylesheet">
<style>
:root{
  --blue:#34a6d7;
  --blue-light:#5cbce6;
  --orange:#f37122;
  --ink:#444;
  --muted:#777;
  --panel:#f3f3f3;
  --line:#e2e2e2;
  --navy:#2c3f8f;
}
*{margin:0;padding:0;box-sizing:border-box}
a{text-decoration:none}
html,body{width:784px;height:1200px;overflow:hidden;background:#fff;font-family:"Open Sans",sans-serif;color:var(--ink)}
.page{position:relative;width:784px;height:1200px}
.abs{position:absolute}

/* header */
.site-header{position:absolute;left:0;top:0;width:784px;height:191px}
.brand{position:absolute;left:312px;top:62px;width:160px;text-align:center;color:#fff;font-family:"Lobster",cursive;font-size:21px;line-height:1}
.brand-dot{display:block;width:34px;height:34px;border-radius:50%;background:#fff;opacity:.85;margin:0 auto 8px}
.main-nav{position:absolute;top:160px;left:0;width:784px;height:22px}
.main-nav a{position:absolute;transform:translateX(-50%);color:#fff;font-family:"Lobster",cursive;font-size:14px;white-space:nowrap}

/* hero */
.hero{position:absolute;left:106px;top:207px;width:572px;height:293px;background:linear-gradient(100deg,#4f7fc8 0%,#4a6fc0 50%,#33408f 100%)}
.hero-photo{position:absolute;left:30px;top:0;width:240px;height:293px;background:radial-gradient(ellipse at 50% 55%,#c9a083 0%,#8d7c9c 45%,rgba(79,127,200,0) 75%)}
.hero-title{position:absolute;left:304px;top:92px;font-family:"Lobster",cursive;font-weight:400;font-size:26px;color:#fff;white-space:nowrap}
.hero-title span{color:var(--orange)}
.hero-text{position:absolute;left:308px;top:130px;width:220px;font-family:"Lobster",cursive;font-size:11.5px;line-height:15px;color:#fff;white-space:nowrap}
.btn{display:inline-block;border-radius:14px;font-family:"Lobster",cursive;color:#fff;text-align:center}
.hero-btn{position:absolute;left:309px;top:188px;width:84px;height:25px;line-height:25px;background:var(--orange);font-size:12px}

/* content */
.section-title{font-family:"Lobster",cursive;font-weight:400;font-size:19px;color:#555}
.theatre-title{left:105px;top:507px}
.theatre-lede{left:106px;top:539px;font-family:"Lobster",cursive;font-size:10.5px;color:var(--orange);white-space:nowrap}
.theatre-body{left:106px;top:558px;width:420px;font-size:7px;line-height:12.3px;color:var(--muted)}
.theatre-btn{left:106px;top:618px;width:64px;height:23px;line-height:23px;background:var(--blue);font-size:10.5px}
.divider{left:106px;top:661px;width:422px;height:1px;background:var(--line)}
.video-title{left:105px;top:674px}
.video{left:106px;top:710px;width:422px;height:218px;background:linear-gradient(135deg,#2f4fa0 0%,#6b7cc0 40%,#c8b46a 65%,#8fbf5a 85%,#3f5fb0 100%)}
.play{position:absolute;left:186px;top:84px}
.testimonial{left:106px;top:950px;width:422px;height:119px;background:var(--panel)}
.testimonial h3{position:absolute;left:17px;top:9px;font-family:"Lobster",cursive;font-weight:400;font-size:19px;color:#555}
.testimonial .arrows{position:absolute;left:383px;top:17px}
.testimonial blockquote{position:absolute;left:18px;top:40px;width:390px;font-size:6.6px;line-height:12.2px;font-style:italic;color:var(--navy)}
.testimonial cite{position:absolute;left:20px;top:95px;font-size:7.5px;font-style:normal;font-weight:600;color:var(--orange)}

/* sidebar */
.widget{position:absolute;left:543px;width:135px;border:1px solid var(--line);overflow:hidden}
.widget-head{height:30px;line-height:30px;padding-left:9px;font-family:"Lobster",cursive;font-size:13.5px;color:#fff}
.events{top:514px;height:206px}
.events .widget-head{background:var(--blue)}
.event{position:relative;height:58px;border-bottom:1px solid var(--line)}
.event:last-child{border-bottom:0}
.event-thumb{position:absolute;left:9px;top:10px;width:44px;height:35px}
.event p{position:absolute;left:60px;top:8px;width:66px;font-size:5.8px;line-height:10px;color:var(--muted)}
.event time{display:block;font-family:"Lobster",cursive;color:var(--orange);font-size:5.5px}
.newsletter{top:728px;height:154px;background:var(--orange);border:0}
.newsletter .widget-head{height:28px}
.newsletter p{padding:6px 10px 0;font-size:5.8px;line-height:10px;color:#fff}
.field{position:absolute;left:11px;width:114px;height:22px;background:#fff;font-size:6px;color:#666;padding:8px 5px 0}
.sub-btn{position:absolute;left:10px;top:119px;width:92px;height:23px;line-height:21px;border:1.5px solid #fff;border-radius:12px;font-size:10px}
.tweets{top:893px;height:176px}
.tweets .widget-head{color:#555;height:28px;font-size:13.5px}
.follow{position:absolute;right:5px;top:9px;width:32px;height:10px;border:1px solid #ccc;border-radius:2px;background:#f6f6f6;font-size:5px;line-height:8px;text-align:center;color:#333}
.tweet{position:relative;height:66px;border-bottom:1px solid var(--line);margin-right:8px}
.tweet:nth-of-type(2){border-bottom:0;height:58px}
.tweet-thumb{position:absolute;left:9px;top:6px;width:22px;height:28px;background:linear-gradient(160deg,#9a6b3a,#2d6cb5 60%,#f37122)}
.tweet .who{position:absolute;left:36px;top:6px;font-size:5.4px;line-height:8px;color:#333}
.tweet .date{position:absolute;right:2px;top:6px;font-size:5px;color:#333}
.tweet p{position:absolute;left:36px;top:24px;width:84px;font-size:5.6px;line-height:9.6px;color:var(--muted)}
.tweet p span{color:var(--blue);font-style:italic}
.scroll{position:absolute;right:1px;top:29px;width:6px;height:120px;background:#f1f1f1}
.scroll i{display:block;width:6px;height:10px;background:#ccc;margin-top:6px}
.tweet-to{position:absolute;left:5px;bottom:3px;width:124px;height:15px;border:1px solid var(--line);background:#fff;font-size:6px;line-height:13px;text-align:center;color:#333}

/* footer */
.site-footer{position:absolute;left:0;top:1100px;width:784px;height:100px}
.social{position:absolute;top:1124px;left:345px;display:flex;gap:4px}
.social span{width:20px;height:20px;border:1.5px solid #fff;border-radius:50%}
.foot-links,.foot-contact,.foot-copy{position:absolute;left:0;width:784px;text-align:center;color:#fff;font-size:6.8px}
.foot-links{top:1156px}
.foot-contact{top:1170px}
.foot-copy{top:1184px;font-size:6px}
</style>
</head>
<body>
<div class="page">

<header class="site-header">
  <svg width="784" height="191" viewBox="0 0 784 191">
    <defs>
      <radialGradient id="sky" cx="50%" cy="55%" r="70%">
        <stop offset="0" stop-color="#5cbce6"/>
        <stop offset="1" stop-color="#34a6d7"/>
      </radialGradient>
    </defs>
    <rect width="784" height="191" fill="url(#sky)"/>
    <path d="M0,116 Q392,170 784,116 L784,191 L0,191 Z" fill="var(--orange)"/>
  </svg>
  <div class="brand"><span class="brand-dot"></span>Benny Bounce</div>
  <nav class="main-nav">
    <a href="#" style="left:138px">Home</a>
    <a href="#" style="left:237px">Balloon Shows</a>
    <a href="#" style="left:366px">Balloon Twisting</a>
    <a href="#" style="left:474px">Theatre</a>
    <a href="#" style="left:557px">Reviews</a>
    <a href="#" style="left:640px">Contact</a>
  </nav>
</header>

<section class="hero">
  <div class="hero-photo" role="img" aria-label="Photo of the entertainer holding colourful balloon animals"></div>
  <h1 class="hero-title">Benny <span>Whistlewood</span></h1>
  <p class="hero-text">Sed ut perspiciatis unde omnis iste<br>natu s error sit voluptatem accusantum<br>doloremque lauda.</p>
  <a class="btn hero-btn" href="#">Read More</a>
</section>

<h2 class="abs section-title theatre-title">Theatre Performance</h2>
<p class="abs theatre-lede">Sed ut perspiciatis unde omnis iste natus error sit voluptatem accu santium doloremque laudan</p>
<p class="abs theatre-body">Sed ut perspiciatis unde omnis iste natus error sit voluptatem accusantium doloremque laudantium, totam rem aperiam, eaque ipsa quae ab illo inventore veritatis.Nemo enim ipsam voluptatem quia voluptas sit aspernatur aut odit aut fugit,d ut perspiciatis unde omnis iste natus error sit voluptatem accusantium doloremque laudantium, totam rem aperiamSed ut perspiciatis unde omnis iste natus error sit voluptatem accusantium doloremque laudantium, totam rem aperiam, eaque</p>
<a class="abs btn theatre-btn" href="#">Read More</a>
<div class="abs divider"></div>

<h2 class="abs section-title video-title">Our Video</h2>
<div class="abs video" role="img" aria-label="Video still of the entertainer surrounded by long twisting balloons">
  <svg class="play" width="50" height="50" viewBox="0 0 50 50"><circle cx="25" cy="25" r="23" fill="rgba(0,0,0,.25)" stroke="#fff" stroke-width="2.5"/><polygon points="20,15 20,35 35,25" fill="#fff"/></svg>
</div>

<section class="abs testimonial">
  <h3>Testimonial</h3>
  <svg class="arrows" width="24" height="10" viewBox="0 0 24 10">
    <circle cx="5" cy="5" r="4.3" fill="none" stroke="var(--orange)" stroke-width="1.3"/><path d="M6.5,2.8 L4,5 L6.5,7.2" fill="none" stroke="var(--orange)" stroke-width="1.3"/>
    <circle cx="18" cy="5" r="4.3" fill="none" stroke="var(--orange)" stroke-width="1.3"/><path d="M16.5,2.8 L19,5 L16.5,7.2" fill="none" stroke="var(--orange)" stroke-width="1.3"/>
  </svg>
  <blockquote>“ Sed ut perspiciatis unde omnis iste natus error sit voluptatem accusantium doloremque laudantium, totam rem aperiam, eaq ue ipsa quae ab illo inventore veritatis et quasi architecto beatae vitae dicta sunt explicabo. Nemo enim ipsam voluptatem quia voluptas sit aspernatur aut odit aut fugit, sed quia consequuntur magni dolores eos qui ratione voluptatem sequi nesciunt. Neque porro quisquam est, qui dolorem ipsum quia dolor sit amet, consectetur, adipisc ”</blockquote>
  <cite>Jhon Smit, city Name</cite>
</section>

<aside class="widget events">
  <div class="widget-head">Upcoming Events</div>
  <div class="event"><div class="event-thumb" role="img" aria-label="Event photo of the entertainer on stage" style="background:linear-gradient(135deg,#2d5fb8,#a7c4e8)"></div><p>Lorem ipsum dom etcons ectetur adipis cing elitseddoei<time>Oct 28 2015</time></p></div>
  <div class="event"><div class="event-thumb" role="img" aria-label="Event photo with colourful balloons" style="background:linear-gradient(135deg,#3a4fa8,#e8b23a 60%,#c23a3a)"></div><p>Lorem ipsum dom etcons ectetur adipis cing elitseddoei<time>Oct 28 2015</time></p></div>
  <div class="event"><div class="event-thumb" role="img" aria-label="Event photo with pink balloon pigs" style="background:linear-gradient(135deg,#f0c8d0,#e58aa0 60%,#d9c2a8)"></div><p style="top:14px">Lorem ipsum dom etcons ectetur<time>Oct 28 2015</time></p></div>
</aside>

<aside class="widget newsletter">
  <div class="widget-head">Newsletter Signup</div>
  <p>Lorem ipsum dom etcons ecteturpis cing elitseddom etcons ectei.</p>
  <div class="field" style="top:64px">Name:</div>
  <div class="field" style="top:91px">Email:</div>
  <a class="btn sub-btn" href="#">Subscribe Now</a>
</aside>

<aside class="widget tweets">
  <div class="widget-head">Tweets</div>
  <span class="follow">Follow</span>
  <div class="scroll"><i></i></div>
  <div class="tweet"><div class="tweet-thumb" role="img" aria-label="Profile picture"></div><span class="who">Benny Whistlewood<br><span style="color:#aaa">@B_Whistle</span></span><span class="date">6 Nov</span><p>Lorem ipsum dometcons tetur adipiscing <span>@Benny Whistlewood</span></p></div>
  <div class="tweet"><div class="tweet-thumb" role="img" aria-label="Profile picture"></div><span class="who">Benny Whistlewood<br><span style="color:#aaa">@B_Whistle</span></span><span class="date">6 Nov</span><p>Lorem ipsum dometcons tetur adipiscing <span>@Benny Whistlewood</span></p></div>
  <div class="tweet-to">Tweet to @ B-Whistlewood</div>
</aside>

<footer class="site-footer">
  <svg width="784" height="100" viewBox="0 0 784 100">
    <path d="M0,52 Q392,-10 784,52 L784,100 L0,100 Z" fill="var(--orange)"/>
    <path d="M0,60 Q392,-2 784,60 L784,100 L0,100 Z" fill="var(--blue)"/>
  </svg>
</footer>
<div class="social" aria-label="Social links"><span></span><span></span><span></span><span></span></div>
<p class="foot-links">Home &nbsp;|&nbsp; Balloon Shows &nbsp;|&nbsp; Balloon Twisting &nbsp;|&nbsp; Theatre &nbsp;|&nbsp; Reviews &nbsp;|&nbsp; Contact</p>
<p class="foot-contact">Call Us: 0123 -456-780 &nbsp;Location: lorem ispsum dolor site dummy addre . Email:hello@bennybounce.com</p>
<p class="foot-copy">Copyright 2015 &nbsp;All Rights Reserved.</p>

</div>
</body>
</html>
```